Web Page - finishing touches

Take my existing rough draft and make it look professional. The components are in place but the page needs a creative touch with a crisp look, professional fonts, and attractive colors.

We are a bathroom remodeling company whose primary customers are 50 + years old and conservative. Our goal for the home page is to get them to request a free estimate, request a Buyer's Guide, or subscribe to our newsletter.
Updates

Project Deadline Extended
Reason: Our website design deadline has been extended by two days. Thanks!

Target Market(s)

Homeowners 50 + years old

Industry/Entity Type

Conservative

Requirements
Must have
• The TILE-NOVA logo can not be changed.

Everything on the rough draft must be included in the finished design.

```html
<!DOCTYPE html>
<html lang="en">
<head>
<meta charset="utf-8">
<title>Tile-Nova Bathroom Remodeling</title>
<link href="https://fonts.googleapis.com/css2?family=Yanone+Kaffeesatz:wght@400;500&family=Noto+Serif:wght@400&family=Open+Sans:ital,wght@0,400;1,400&display=swap" rel="stylesheet">
<style>
:root{
  --dark:#3a3a3a;
  --black:#111;
  --red:#d9262a;
  --green:#7ab648;
  --pale:#dde9ea;
  --field:#cdd6d9;
  --field-text:#f2f5f6;
  --text:#555;
  --white:#fff;
}
*{margin:0;padding:0;box-sizing:border-box}
html,body{width:1047px;height:1200px;overflow:hidden}
body{position:relative;font-family:"Open Sans",sans-serif;background:var(--white);color:var(--text)}
.abs{position:absolute}
.serif{font-family:"Noto Serif",serif;font-weight:400}
.dot{display:inline-block;border-radius:50%;background:var(--green);vertical-align:middle}
.header{left:0;top:0;width:1047px;height:169px;background:var(--dark)}
.brand{left:113px;top:50px;font-family:"Yanone Kaffeesatz",sans-serif;font-weight:500;font-size:46px;color:var(--red);letter-spacing:1px;line-height:1}
.call{right:120px;top:38px;font-size:18px;color:var(--white);font-family:"Yanone Kaffeesatz",sans-serif;letter-spacing:.5px}
.call .dot{width:10px;height:10px;background:var(--red);margin-right:4px;margin-top:-3px}
.main-nav a,.foot-nav a{position:absolute;color:var(--white);text-decoration:none;font-size:18px;font-family:"Yanone Kaffeesatz",sans-serif}
.main-nav a{top:146px}
.main-nav .home .dot{width:10px;height:10px;background:var(--red);margin:-3px 3px 0 -13px}
.photo{border:2px solid #222}
.hero-photo{left:132px;top:202px;width:393px;height:278px;background:linear-gradient(120deg,#d8c3a6,#c9ad8c 45%,#b9a48e 70%,#9e8d7c)}
.pager{left:303px;top:486px;display:flex;gap:7px}
.pager span{width:11px;height:11px;border:1.5px solid #444;border-radius:50%;background:var(--white)}
.pager span.on{box-shadow:inset 0 0 0 2px #fff;background:#888}
h2{font-weight:400;color:#333}
.hero-title{left:543px;top:205px;font-size:19px}
.hero-title .dot,.sec-title .dot{width:10px;height:10px;margin:-3px 3px 0 0}
.perks{left:559px;top:246px;list-style:none;font-style:italic;font-size:13.5px;line-height:23.5px}
.perks .dot{width:6px;height:6px;margin:-3px 3px 0 0}
.lead{left:546px;top:342px;width:350px;font-size:13.6px;line-height:15.7px}
.btn{position:absolute;background:var(--green);color:var(--white);font-size:14px;border-radius:3px;height:23px;line-height:23px;padding-left:6px}
.contact-band{left:0;top:518px;width:1047px;height:402px;background:var(--pale)}
.sec-title{font-size:21px}
.field{position:absolute;left:117px;width:400px;height:25px;background:var(--field);border-radius:3px;color:var(--field-text);font-size:13.5px;font-weight:600;padding:3px 6px}
.vanity-photo{left:560px;width:329px;height:239px;background:linear-gradient(90deg,#6a4430,#c9a27e 35%,#d9b98f 60%,#4f2e22)}
.caption{left:563px;width:330px;font-size:13.6px;line-height:15.7px}
.footer{left:0;top:920px;width:1047px;height:225px;background:var(--dark);border-top:2px solid #c9302c}
.foot-title{color:var(--white);font-size:21px}
.foot-text{color:var(--white);font-size:11.4px;line-height:13px}
.guide{left:115px;top:147px;width:240px;color:var(--white);font-size:13.5px;line-height:15.5px}
.input{position:absolute;left:389px;width:259px;height:25px;background:var(--field);color:var(--field-text);font-size:13.5px;font-weight:600;padding:3px 6px}
.foot-nav{left:0;top:1145px;width:1047px;height:55px;background:var(--black)}
.foot-nav a{top:8px}
.sep{position:absolute;top:10px;width:2px;height:24px;background:var(--green)}
</style>
</head>
<body>

<header class="abs header">
  <div class="abs brand">TILE-NOVA</div>
  <div class="abs call"><span class="dot"></span>Call Us Today : 555 014 2200</div>
  <nav class="main-nav">
    <a class="home" style="left:122px"><span class="dot"></span>Home</a>
    <a style="left:229px">About Us</a>
    <a style="left:356px">Design Photos</a>
    <a style="left:498px">Products</a>
    <a style="left:612px">Showroom</a>
    <a style="left:744px">Contact Us</a>
    <a style="left:877px">Blog</a>
  </nav>
</header>

<div class="abs photo hero-photo" role="img" aria-label="Remodeled bathroom with glass shower and tiled tub surround"></div>
<div class="abs pager"><span class="on"></span><span></span><span></span><span></span></div>

<h2 class="abs serif hero-title"><span class="dot"></span>Bathroom remodeling by Tile-Nova</h2>
<ul class="abs perks">
  <li><span class="dot"></span>Free design ideas and estimates</li>
  <li><span class="dot"></span>Full service bathroom remodeler</li>
  <li><span class="dot"></span>A+ Rating by the Home Trade Council</li>
  <li><span class="dot"></span>17 Years of experience</li>
</ul>
<p class="abs lead">Whether you need a simple bathtub replacement or a complete bathroom remodel, we can help. We're the Marlow Family and we've remodeled over 8,000 bathrooms in the past 17 years. We offer affordable bathroom remodeling solutions for any budget with attractive payment options. Call us today</p>
<a class="btn" style="left:550px;top:450px;width:84px">Learn More</a>

<section class="abs contact-band">
  <h2 class="abs serif sec-title" style="left:119px;top:32px"><span class="dot"></span>Contact Us</h2>
  <div class="field" style="top:75px">Email</div>
  <div class="field" style="top:107px">Tel</div>
  <div class="field" style="top:138px">Subject</div>
  <div class="field" style="top:170px;height:128px">Content</div>
  <a class="btn" style="left:117px;top:312px;width:85px;padding-left:14px">Submit</a>
  <div class="abs photo vanity-photo" style="top:73px" role="img" aria-label="Bathroom with dark wood double vanity and large mirror"></div>
  <p class="abs caption" style="top:322px">Can Tile-Nova remodel my bathroom in one-day like other companies advertise?</p>
  <a class="btn" style="left:560px;top:359px;width:85px">Learn More</a>
</section>

<footer class="abs footer">
  <h2 class="abs serif foot-title" style="left:119px;top:12px"><span class="dot" style="width:10px;height:10px;margin:-3px 3px 0 0"></span>Testimonials</h2>
  <p class="abs foot-text" style="left:114px;top:50px;width:264px;color:#ddd">"Dan, our installer, is a highly skilled professional. He was courteous, gave attention to detail, and is the model of what a customer would want in the service he provided. Please THANK him again for his workmanship and customer service."</p>
  <p class="abs foot-text" style="left:114px;top:128px;width:257px;text-align:right;font-style:italic">Ellen and Roy Pruitt, Cedar Falls</p>
  <p class="abs guide">Free buyer's Guide for Bathroom Remodeling</p>
  <a class="btn" style="left:113px;top:184px;width:84px">Get it now</a>

  <h2 class="abs serif foot-title" style="left:388px;top:12px"><span class="dot" style="width:10px;height:10px;margin:-3px 3px 0 0"></span>Newsletter</h2>
  <p class="abs foot-text" style="left:388px;top:51px;width:240px">Subscribe to our Newsletter Discounts and Special Offers, Tips, Interesting Articles, and more...</p>
  <div class="input" style="top:101px">Email</div>
  <div class="input" style="top:133px">Name</div>
  <a class="btn" style="left:389px;top:169px;width:85px;padding-left:14px">Submit</a>

  <h2 class="abs serif foot-title" style="left:667px;top:12px"><span class="dot" style="width:10px;height:10px;margin:-3px 3px 0 0"></span>Contact Details</h2>
  <p class="abs foot-text" style="left:667px;top:51px;width:270px">Have a question? We can help.<br>E-mail us or give us a call. We'll respond quickly.</p>
  <div class="abs" style="left:667px;top:92px;color:var(--white);font-size:19px">555-018-4477</div>
  <a class="btn" style="left:667px;top:135px;width:84px;padding-left:14px">Contact</a>
  <svg class="abs" style="left:800px;top:86px" width="140" height="130" viewBox="0 0 140 130" aria-hidden="true">
    <circle cx="56" cy="30" r="28" fill="#5b8fb0" stroke="#cfd8dc" stroke-width="2"/>
    <rect x="92" y="1" width="37" height="81" rx="3" fill="#2f6ea3" stroke="#cfd8dc" stroke-width="1.5"/>
    <circle cx="25" cy="108" r="15" fill="#777"/>
    <circle cx="69" cy="108" r="15" fill="#777"/>
    <circle cx="111" cy="108" r="15" fill="#777"/>
  </svg>
</footer>

<nav class="abs foot-nav">
  <a style="left:122px">Home</a>
  <span class="sep" style="left:196px"></span>
  <a style="left:229px">About Us</a>
  <span class="sep" style="left:323px"></span>
  <a style="left:356px">Design Photos</a>
  <span class="sep" style="left:471px"></span>
  <a style="left:498px">Products</a>
  <span class="sep" style="left:584px"></span>
  <a style="left:612px">Showroom</a>
  <span class="sep" style="left:714px"></span>
  <a style="left:744px">Contact Us</a>
  <span class="sep" style="left:847px"></span>
  <a style="left:877px">Blog</a>
</nav>

</body>
</html>
```